Tarlow Plumbing & Heating Limited needs a service and maintenance contract document design

Tarlow Plumbing & Heating Limited are a well established family owned and operated company.

We currently offer installation, service and repair services for gas, plumbing, heating and electrical work. We wish to offer service and maintenance plans for plumbing, heating and electrical for our domestic clients in the UK. We would like the brochure to incorporate our company logo and colours, and reflect the reliable, quality, 5 star service we offer our clients.
I have attached a brochure that a friends company uses to give a good idea of the structure of the plans we wish to offer. We want to give our customers a choice in what packages best suit their needs. However, the pricing structure and certain elements/content of what we offer will be slightly different due to our geographical location.

We would like to have the basic structure of the brochure put in place and the
text content editable to our specific needs. Looking for advice on this but we do have Acrobat DC if we need to edit the text ourselves?

We use our logo with "TARLOW" in white over a grey backgound.

Our website is - www.tarlow.plumbing
Facebook and twitter handle is - @TarlowHeating

Target Market(s)

UK domestic plumbing, heating, natural gas, LPG and electrical market. Both private homeowners and landlords. Please see both the domestic and landlord document files attached for an idea on what we'd like.

Colors

Designer to choose colors to be used in the design.

Requirements
Must have
• Would like the finished design to incorporate the branding and colours we already use. Professional, Contemporary designs that will stand out above our competition.
• The content of the brochures MUST be very similar in structure to the files I’ve attached to the brief.
• We are having many designs submitted that are just copying our website content. This is not what we are asking for.
• I would like the icons etc to be redesigned so they are ours and not copied.
• Please also see the Landlords brochure attached to the brief. We would like this to be a separate document but to reflect the same design as the homeowner design you submit.
• The content of the documents will need to be re worded for our own use but I'm happy to change this once the design element is in place.
• A4 sized pages as per the example I've attached
• Must be able to attach the document to our website for clients to download.
Nice to have
• A4 sized pages as per the examples I've attached
Should not have
• Please DO NOT copy the content from our website to create our service plan brochures. This is not what we are after. As above, we need the brochures to be like the ones we've provided but made to fit our brand.
• Thank you

```html
<!DOCTYPE html>
<html lang="en">
<head>
<meta charset="utf-8">
<title>Tarlow Plumbing &amp; Heating – Home Comfort plans at a glance</title>
<link href="https://fonts.googleapis.com/css2?family=Oswald:wght@400;500&family=Roboto+Condensed:wght@300;400;700&family=Caveat:wght@400&family=Roboto:wght@700;900&display=swap" rel="stylesheet">
<style>
  :root{
    --backdrop:#414143;
    --paper:#ffffff;
    --paper-shade:#e2e2e4;
    --ink:#231f20;
    --ink-soft:#4a4a4c;
    --panel:#1d1d1f;
    --orange:#e8641e;
    --orange-light:#f89a1c;
    --blue:#29a9e1;
    --blue-deep:#1570b7;
    --navy:#1f2a4a;
    --rule:#6d6d6f;
  }
  *{margin:0;padding:0;box-sizing:border-box}
  html,body{width:1200px;height:884px;overflow:hidden;background:var(--backdrop)}
  .spread{position:relative;width:1200px;height:884px}
  .page{position:absolute;top:78px;width:516px;height:728px;
    background:linear-gradient(90deg,var(--paper-shade) 0%,var(--paper) 30%,var(--paper) 100%)}
  .page--left{left:80px}
  .page--right{left:604px}
  .abs{position:absolute}

  .brand{position:absolute;display:flex;align-items:center;gap:7px;
    font-family:"Roboto",sans-serif;font-weight:900;font-size:27px;color:var(--navy);letter-spacing:.5px}
  .brand__dot{width:28px;height:28px;border-radius:50%;background:var(--orange)}

  .rule{position:absolute;height:1px;background:var(--rule)}
  .script{font-family:"Caveat",cursive;color:var(--ink)}
  .folio{position:absolute;font-family:"Roboto Condensed",sans-serif;font-weight:700;font-size:10px;color:var(--ink)}

  .title{position:absolute;left:104px;top:178px;font-family:"Oswald",sans-serif;font-weight:500;
    font-size:53px;line-height:73px;color:var(--orange)}
  .copy{position:absolute;font-family:"Roboto Condensed",sans-serif;font-weight:300;font-size:9px;line-height:12.5px;color:var(--ink-soft)}
  .copy p{margin-bottom:11px}
  .copy strong{font-weight:700;color:var(--ink)}

  .panel{position:absolute;background:var(--panel)}
  .panel--bleed{border-radius:24px 0 0 24px}
  .panel--card{border-radius:16px}
  .panel-head{position:absolute;font-family:"Roboto Condensed",sans-serif;font-weight:700;font-size:11px;color:#fff;white-space:nowrap}
  .panel-head b{font-family:"Oswald",sans-serif;font-weight:500;font-size:16px}
  .panel-head--right{text-align:right}
  .section-head{position:absolute;font-family:"Oswald",sans-serif;font-weight:500;font-size:16px;color:var(--ink)}
  .plan-head{position:absolute;font-family:"Oswald",sans-serif;font-weight:400;font-size:10px;color:var(--orange);white-space:nowrap}
  .pack-label{position:absolute;font-family:"Roboto Condensed",sans-serif;font-weight:700;font-size:10px;line-height:16px;color:var(--ink)}
  .pack-label b{font-family:"Oswald",sans-serif;font-weight:500;font-size:14px}
  .pack-label--dark{color:#fff}
  .divider{position:absolute;width:1px;background:#b5b5b7}
  .card-rule{position:absolute;left:913px;width:176px;height:1px;background:#9a9a9c}

  /* plan badge: round token above a caption pill */
  .badge{position:absolute;width:58px;height:72px}
  .badge__token{position:absolute;left:5px;top:0;width:48px;height:48px;border-radius:50%;
    display:flex;align-items:center;justify-content:center;border:2px solid #fff;
    background:linear-gradient(180deg,var(--orange),var(--orange-light));
    font-family:"Roboto",sans-serif;font-weight:700;font-size:19px;color:#fff}
  .badge__token--icon{background:var(--blue-deep)}
  .badge__token svg{width:24px;height:24px}
  .badge__caption{position:absolute;left:0;right:0;top:54px;height:16px;border-radius:8px;
    background:var(--blue);display:flex;align-items:center;justify-content:center;text-align:center;
    font-family:"Roboto Condensed",sans-serif;font-weight:700;font-size:7px;line-height:7px;color:#fff;white-space:nowrap}

  .save-sub{position:absolute;font-family:"Roboto",sans-serif;font-weight:700;font-size:14px;color:var(--orange)}
  .card-title{position:absolute;font-family:"Oswald",sans-serif;font-weight:400;font-size:12.5px;color:var(--orange)}
  .card-copy{position:absolute;font-family:"Roboto Condensed",sans-serif;font-weight:300;font-size:9px;line-height:12.5px;color:#fff}
</style>
</head>
<body>
<svg width="0" height="0" style="position:absolute" aria-hidden="true">
  <defs>
    <symbol id="i-tools" viewBox="0 0 20 20"><g fill="none" stroke="#fff" stroke-width="1.4"><path d="M4 16 15 5"/><path d="M4 4 16 16"/><circle cx="15.5" cy="4.5" r="2.2"/></g></symbol>
    <symbol id="i-boiler" viewBox="0 0 20 20"><g fill="none" stroke="#fff" stroke-width="1.4"><rect x="5" y="2" width="10" height="14" rx="1"/><path d="M7 12h6M8 16v3M12 16v3"/></g></symbol>
    <symbol id="i-dial" viewBox="0 0 20 20"><g fill="none" stroke="#fff" stroke-width="1.4"><circle cx="10" cy="10" r="7"/><path d="M10 10l4-4"/></g></symbol>
    <symbol id="i-radiator" viewBox="0 0 20 20"><g fill="none" stroke="#fff" stroke-width="1.4"><rect x="2" y="5" width="16" height="10"/><path d="M5.5 5v10M9 5v10M12.5 5v10M16 5v10"/></g></symbol>
    <symbol id="i-tap" viewBox="0 0 20 20"><g fill="none" stroke="#fff" stroke-width="1.4"><path d="M3 8h9v4M8 5v3M6 5h4M12 15v1M12 18v1"/></g></symbol>
    <symbol id="i-grid" viewBox="0 0 20 20"><g fill="none" stroke="#fff" stroke-width="1.2"><rect x="3" y="3" width="14" height="14"/><path d="M3 7.7h14M3 12.3h14M7.7 3v14M12.3 3v14"/></g></symbol>
    <symbol id="i-gas" viewBox="0 0 20 20"><g fill="none" stroke="#fff" stroke-width="1.4"><circle cx="10" cy="6" r="4"/><path d="M10 10v5M3 15h14"/></g></symbol>
    <symbol id="i-plug" viewBox="0 0 20 20"><g fill="none" stroke="#fff" stroke-width="1.4"><path d="M5 9l5-5 5 5-5 5zM3 17l4-4M9 4l2-2M15 10l2-2"/></g></symbol>
    <symbol id="i-fire" viewBox="0 0 20 20"><g fill="none" stroke="#fff" stroke-width="1.3"><rect x="3" y="3" width="14" height="14"/><rect x="6" y="8" width="8" height="9"/><path d="M10 15c-2 0-2-2 0-4 2 2 2 4 0 4z"/></g></symbol>
  </defs>
</svg>

<div class="spread">
  <div class="page page--left"></div>
  <div class="page page--right"></div>

  <!-- Left page -->
  <div class="abs script" style="left:110px;top:118px;font-size:20px">We care</div>
  <div class="brand" style="left:386px;top:103px"><span class="brand__dot"></span>TARLOW</div>
  <div class="rule" style="left:104px;top:144px;width:468px"></div>

  <h1 class="title">The Home<br>Comfort<br>plans at a<br>glance</h1>

  <div class="copy" style="left:104px;top:511px;width:222px">
    <p>The diagrams to the right illustrate the different plans and combination packs available from Home Comfort, and how they might work together.</p>
    <p><strong>Our Boiler Service plan will always form the foundation of your chosen package. After that, you’re free to add as few or as many plans and/or combination packs as you like, to create a completely bespoke package that meets your household’s needs.</strong></p>
    <p>The monthly cost for each plan and combination pack is shown in the diagrams to the right. To work out how much you’ll need to pay in total for each month, simply add up the costs that apply to your chosen plans and/or combination packs.</p>
  </div>

  <div class="panel panel--bleed" style="left:366px;top:184px;width:230px;height:242px"></div>
  <div class="panel-head panel-head--right" style="right:630px;top:197px">Foundation Plan</div>
  <div class="badge" style="left:512px;top:222px"><span class="badge__token">£5</span><span class="badge__caption">Boiler Service</span></div>
  <div class="panel-head panel-head--right" style="right:630px;top:300px">Heating Maintenance Plans</div>
  <div class="badge" style="left:392px;top:324px"><span class="badge__token">£6</span><span class="badge__caption">Boiler</span></div>
  <div class="badge" style="left:452px;top:324px"><span class="badge__token">£3</span><span class="badge__caption">Controls</span></div>
  <div class="badge" style="left:512px;top:324px"><span class="badge__token">£3</span><span class="badge__caption">Central heating</span></div>

  <h2 class="section-head" style="right:630px;top:448px">Our Combination Packs</h2>

  <div class="panel panel--bleed" style="left:366px;top:491px;width:230px;height:242px"></div>
  <div class="panel-head panel-head--right" style="right:630px;top:512px">Heating Twin Pack <b>£5</b></div>
  <div class="badge" style="left:450px;top:540px"><span class="badge__token badge__token--icon"><svg><use href="#i-dial"/></svg></span><span class="badge__caption">Controls</span></div>
  <div class="badge" style="left:512px;top:540px"><span class="badge__token badge__token--icon"><svg><use href="#i-radiator"/></svg></span><span class="badge__caption">Central heating</span></div>
  <div class="panel-head panel-head--right" style="right:630px;top:614px">Heating Triple Pack <b>£10</b></div>
  <div class="badge" style="left:392px;top:642px"><span class="badge__token badge__token--icon"><svg><use href="#i-boiler"/></svg></span><span class="badge__caption">Boiler</span></div>
  <div class="badge" style="left:452px;top:642px"><span class="badge__token badge__token--icon"><svg><use href="#i-dial"/></svg></span><span class="badge__caption">Controls</span></div>
  <div class="badge" style="left:512px;top:642px"><span class="badge__token badge__token--icon"><svg><use href="#i-radiator"/></svg></span><span class="badge__caption">Central heating</span></div>

  <div class="rule" style="left:104px;top:764px;width:468px"></div>
  <div class="folio" style="left:110px;top:772px">Page 4</div>

  <!-- Right page -->
  <div class="brand" style="left:910px;top:103px"><span class="brand__dot"></span>TARLOW</div>
  <div class="rule" style="left:628px;top:144px;width:300px"></div>

  <div class="plan-head" style="left:623px;top:164px">Water Maintenance Plans</div>
  <div class="plan-head" style="left:725px;top:164px">Energy Maintenance Plans</div>
  <div class="plan-head" style="left:827px;top:164px">Gas Fire Plan</div>
  <div class="divider" style="left:712px;top:192px;height:140px"></div>
  <div class="divider" style="left:804px;top:192px;height:140px"></div>

  <div class="badge" style="left:638px;top:186px"><span class="badge__token">£3</span><span class="badge__caption">Plumbing</span></div>
  <div class="badge" style="left:638px;top:266px"><span class="badge__token">£3</span><span class="badge__caption">Drains</span></div>
  <div class="badge" style="left:729px;top:186px"><span class="badge__token">£5</span><span class="badge__caption">Gas pipe</span></div>
  <div class="badge" style="left:729px;top:266px"><span class="badge__token">£5</span><span class="badge__caption">Electrics</span></div>
  <div class="badge" style="left:822px;top:186px"><span class="badge__token">£5</span><span class="badge__caption">Gas fire (per fire)</span></div>

  <div class="pack-label" style="left:648px;top:393px">+ Water<br>Pack <b>£5</b></div>
  <div class="badge" style="left:707px;top:373px"><span class="badge__token">£6</span><span class="badge__caption">Boiler</span></div>
  <div class="badge" style="left:767px;top:373px"><span class="badge__token">£3</span><span class="badge__caption">Controls</span></div>
  <div class="pack-label" style="left:648px;top:475px">+ Water<br>Pack <b>£5</b></div>
  <div class="badge" style="left:707px;top:455px"><span class="badge__token">£6</span><span class="badge__caption">Boiler</span></div>
  <div class="badge" style="left:767px;top:455px"><span class="badge__token">£3</span><span class="badge__caption">Controls</span></div>

  <div class="abs script" style="left:630px;top:535px;font-size:25px">Save money</div>
  <div class="save-sub" style="left:630px;top:566px">with Combination Packs</div>
  <div class="copy" style="left:630px;top:594px;width:260px">
    <p>As you can see, we’ve put some of our plans together to create money-saving combination packs, which cost less per month than buying each plan individually. You’ll find out more about these on pages 8, 9, 11 and 13.</p>
    <p style="margin-top:14px;margin-bottom:14px"><strong>Building your Home Comfort package</strong></p>
    <p>As long as your package includes our Boiler Service plan, you’re free to mix and match our other plans and combination packs as you choose, to create your very own, customised Home Comfort package.</p>
  </div>

  <div class="panel panel--card" style="left:902px;top:149px;width:198px;height:585px"></div>
  <div class="card-title" style="left:914px;top:163px">The full Home Comfort Package</div>
  <div class="card-copy" style="left:914px;top:186px;width:172px">If you choose the full Home Comfort package as shown in the diagram below, your monthly payment to us will be just £25 per month.</div>
  <div class="card-rule" style="top:237px"></div>
  <div class="pack-label pack-label--dark" style="left:913px;top:277px">Foundation Plan</div>
  <div class="badge" style="left:1032px;top:252px"><span class="badge__token">£5</span><span class="badge__caption">Boiler Service</span></div>
  <div class="card-rule" style="top:333px"></div>
  <div class="pack-label pack-label--dark" style="left:913px;top:347px">+ Heating Triple Pack <b>£10</b></div>
  <div class="badge" style="left:911px;top:374px"><span class="badge__token badge__token--icon"><svg><use href="#i-boiler"/></svg></span><span class="badge__caption">Boiler</span></div>
  <div class="badge" style="left:971px;top:374px"><span class="badge__token badge__token--icon"><svg><use href="#i-dial"/></svg></span><span class="badge__caption">Controls</span></div>
  <div class="badge" style="left:1032px;top:374px"><span class="badge__token badge__token--icon"><svg><use href="#i-radiator"/></svg></span><span class="badge__caption">Central heating</span></div>
  <div class="card-rule" style="top:454px"></div>
  <div class="pack-label pack-label--dark" style="left:913px;top:489px">+ Water<br>Pack <b>£5</b></div>
  <div class="badge" style="left:971px;top:469px"><span class="badge__token badge__token--icon"><svg><use href="#i-tap"/></svg></span><span class="badge__caption">Plumbing</span></div>
  <div class="badge" style="left:1032px;top:469px"><span class="badge__token badge__token--icon"><svg><use href="#i-grid"/></svg></span><span class="badge__caption">Drains</span></div>
  <div class="card-rule" style="top:550px"></div>
  <div class="pack-label pack-label--dark" style="left:913px;top:585px">+ Energy<br>Pack <b>£5</b></div>
  <div class="badge" style="left:971px;top:565px"><span class="badge__token badge__token--icon"><svg><use href="#i-gas"/></svg></span><span class="badge__caption">Gas pipe</span></div>
  <div class="badge" style="left:1032px;top:565px"><span class="badge__token badge__token--icon"><svg><use href="#i-plug"/></svg></span><span class="badge__caption">Electrics</span></div>
  <div class="card-copy" style="left:913px;top:650px;width:112px">If you’d also like us to cover one or more gas fires in your home, you’ll need to add on a monthly cost of £5 per fire to this total.</div>
  <div class="badge" style="left:1032px;top:648px"><span class="badge__token">£5</span><span class="badge__caption">Gas fire (per fire)</span></div>

  <div class="rule" style="left:628px;top:764px;width:466px"></div>
  <div class="folio" style="right:107px;top:772px">Page 5</div>
</div>
</body>
</html>
```